Rack Card for Bright Meadow Dog Training

I love the logo you designed for me a while back (I had it updated and have the new files).

I need a rack card designed, 2 sided.

One side will be Bright Meadow Dog Training (my general dog training business)

The other side will be my Deaf and Blind Dog Training Business speciality.

Both sides Full Color/4 color

3.5 x 8.5 inches

I can provide photos and text accordingly.

Let me know the estimated price and Turn around time.

```html
<!DOCTYPE html>
<html lang="en">
<head>
<meta charset="utf-8">
<title>Bright Meadow Dog Training – Rack Cards</title>
<link rel="stylesheet" href="https://fonts.googleapis.com/css2?family=Poppins:wght@400;500;600;700;800&display=swap">
<style>
  :root{
    --stage:#c4c4c4;
    --ink:#33342f;
    --ink-soft:#45463f;
    --cream:#eeebdf;
    --paper:#ffffff;
    --photo-warm:#b98a5a;
    --photo-dark:#2b2622;
    --photo-green:#8fa65b;
    --photo-sky:#a9c2cc;
  }
  *{margin:0;padding:0;box-sizing:border-box}
  html,body{width:943px;height:1200px;overflow:hidden;background:var(--stage);font-family:"Poppins",sans-serif;color:var(--ink)}
  .rack-card{position:absolute;top:176px;width:349px;height:848px;background:var(--cream);overflow:hidden}
  .rack-card--general{left:97px}
  .rack-card--special{left:497px}
  .abs{position:absolute}
  .card-shape{position:absolute;left:0;top:0}
  .brand{position:absolute;display:flex;align-items:center;gap:6px;font-size:13px;font-weight:500;color:var(--ink);line-height:1.1}
  .brand-dot{width:14px;height:14px;border-radius:50%;background:var(--ink);flex:none}
  .headline{position:absolute;font-size:21px;line-height:22px;font-weight:400;text-transform:uppercase;letter-spacing:-.2px}
  .headline b{font-weight:700}
  .photo{position:absolute}
  .photo--round{border-radius:50%;border:3px solid var(--ink)}
  .section-title{position:absolute;font-size:12.5px;font-weight:700;text-transform:uppercase;padding-bottom:3px;border-bottom:1px solid var(--ink)}
  .bullets{position:absolute;list-style:none;font-size:9.4px;line-height:11px;color:var(--ink-soft)}
  .bullets li{position:relative;padding-left:16px;margin-bottom:8px}
  .bullets li::before{content:"";position:absolute;left:2px;top:3px;width:6px;height:6px;border-radius:50%;background:var(--ink)}
  .bullets--tight li{margin-bottom:0}
  .services{position:absolute;left:179px;top:273px;width:151px;height:283px;background:var(--ink);border-radius:8px}
  .services-tag{position:absolute;left:9px;top:0;width:133px;height:62px;background:var(--cream);clip-path:polygon(0 0,100% 0,100% 82%,50% 100%,0 82%);text-align:center;font-size:8px;line-height:9.5px;padding:8px 4px 0;text-transform:uppercase}
  .services-tag b{font-weight:700}
  .services-list{position:absolute;left:9px;top:68px;width:130px;list-style:none}
  .services-list li{display:flex;align-items:center;gap:8px;height:30px;border-bottom:1px solid #55564f;color:var(--paper);font-size:9.2px;font-weight:600;line-height:10.5px}
  .services-list li:last-child{border-bottom:none}
  .svc-icon{width:20px;height:20px;border-radius:50%;border:1.5px solid var(--paper);flex:none}
  .private-note{position:absolute;left:18px;top:558px;font-size:10.4px;line-height:12.5px}
  .private-note b{font-weight:700}
  .cta{position:absolute;left:18px;top:705px;color:var(--paper);font-size:15.5px;line-height:17px;text-transform:uppercase}
  .cta b{font-weight:700}
  .contacts{position:absolute;left:19px;top:746px;color:var(--paper);font-size:8.6px;line-height:12px}
  .contact-city{display:flex;align-items:center;gap:5px;text-transform:uppercase}
  .contact-phone{display:flex;align-items:center;gap:5px;font-size:10.2px;font-weight:700;margin-bottom:13px}
  .trainer{position:absolute;left:133px;top:747px;color:var(--paper);font-size:10.5px;line-height:12.5px}
  .trainer-name{display:inline-block;background:var(--paper);color:var(--ink);font-weight:700;font-size:10px;padding:0 5px;margin-bottom:4px;text-transform:uppercase}
  .site{position:absolute;left:20px;top:824px;color:var(--paper);font-size:11.4px;font-weight:700}
</style>
</head>
<body>

<section class="rack-card rack-card--general">
  <svg class="card-shape" width="349" height="848" viewBox="0 0 349 848" aria-hidden="true">
    <path d="M0 0H349V244C300 262 250 262 205 248C150 230 90 208 0 222Z" fill="var(--paper)"/>
    <path d="M0 222C90 188 150 214 205 238C250 256 300 255 349 226V244C300 262 250 262 205 248C150 230 90 208 0 232Z" fill="var(--ink)"/>
    <path d="M0 632C60 618 130 650 200 640C260 632 300 600 349 608V848H0Z" fill="var(--ink)"/>
  </svg>

  <div class="brand" style="left:19px;top:40px"><span class="brand-dot"></span>Bright<br>Meadow</div>
  <h1 class="headline" style="left:18px;top:115px">Dog <b>Training</b><br><b>&amp; Behavioral</b><br>Science Services</h1>
  <div class="photo" role="img" aria-label="Black and tan puppy sitting" style="left:216px;top:50px;width:126px;height:176px;border-radius:50% 50% 30% 30%;background:radial-gradient(circle at 50% 40%,var(--photo-dark),#1a1715 70%,transparent 72%)"></div>

  <h2 class="section-title" style="left:20px;top:230px">Train Don’t Blame!</h2>
  <ul class="bullets" style="left:19px;top:257px;width:145px">
    <li>We teach dogs of all ages: Puppies, Adolescents &amp; Adults.</li>
    <li>Become the “Pack Guardian”. Read your dog’s signals (body language, signs of anxiety, etc.) and how to motivate him.</li>
    <li>Use structured play and games to obtain desired behavior and have fun with your dog.</li>
    <li>Good manners – what all good dogs should know.</li>
    <li>Proper leash and obedience skills (no pulling or lunging).</li>
    <li>How to handle ‘real-world experiences’ (skateboards, loud noises, meet and greet new people and dogs, etc.).</li>
  </ul>
  <div class="abs" style="left:17px;top:549px;width:153px;border-top:1px solid var(--ink)"></div>

  <div class="services">
    <div class="services-tag">We specialize helping<br><b>reactive, aggressive, fearful and anxious dogs</b></div>
    <ul class="services-list">
      <li><span class="svc-icon"></span>Puppy Training</li>
      <li><span class="svc-icon"></span>House Breaking</li>
      <li><span class="svc-icon"></span>Leash Training</li>
      <li><span class="svc-icon"></span>Obedience</li>
      <li><span class="svc-icon"></span>Rescue Dog<br>Training</li>
      <li><span class="svc-icon"></span>Separation<br>Anxiety</li>
      <li><span class="svc-icon"></span>Socialization</li>
    </ul>
    <div class="photo" role="img" aria-label="Merle puppy jumping" style="left:103px;top:185px;width:48px;height:98px;border-radius:0 0 8px 0;background:linear-gradient(#b9b4ae,#7d766f)"></div>
  </div>

  <p class="private-note">Private Custom Dog Training<br>Lessons In <b>Person or via<br>MeetLine Sessions</b></p>

  <div class="photo photo--round" role="img" aria-label="Hound puppy standing on grass" style="left:19px;top:611px;width:76px;height:76px;background:linear-gradient(var(--photo-sky),var(--photo-green))"></div>
  <div class="photo photo--round" role="img" aria-label="Red hound dog portrait" style="left:100px;top:627px;width:76px;height:76px;background:radial-gradient(circle,var(--photo-warm),#5a3a24)"></div>
  <div class="photo photo--round" role="img" aria-label="Happy mixed breed dog outdoors" style="left:175px;top:595px;width:76px;height:76px;background:linear-gradient(#c9c9b5,#7b6a55)"></div>
  <div class="photo photo--round" role="img" aria-label="Brown and white terrier resting" style="left:253px;top:573px;width:76px;height:76px;background:linear-gradient(#d9cfc3,#8a5432)"></div>

  <div class="photo" role="img" aria-label="Trainer kneeling with a shepherd dog" style="left:245px;top:667px;width:104px;height:181px;background:linear-gradient(160deg,#8c7a66,#4b5166 60%,#7a6045)"></div>

  <p class="cta">Schedule <b>Free 30 Minute</b><br>Phone Consultation With</p>
  <div class="contacts">
    <div class="contact-city"><svg width="9" height="10" viewBox="0 0 9 10"><path d="M4.5 0a3.3 3.3 0 0 1 3.3 3.3C7.8 5.6 4.5 8.2 4.5 8.2S1.2 5.6 1.2 3.3A3.3 3.3 0 0 1 4.5 0Z" fill="var(--paper)"/><circle cx="4.5" cy="3.3" r="1.2" fill="var(--ink)"/><rect x="0" y="9" width="9" height="1" fill="var(--paper)"/></svg>Los Angeles</div>
    <div class="contact-phone"><svg width="10" height="10" viewBox="0 0 10 10"><circle cx="5" cy="5" r="4.3" fill="none" stroke="var(--paper)" stroke-width="1.2"/><path d="M3.4 2.8l1 1-.6.8c.4.8 1 1.4 1.7 1.8l.8-.6 1 1-.8.9C4.9 7.5 2.6 5.3 2.5 3.5Z" fill="var(--paper)"/></svg>(310) 555-0142</div>
    <div class="contact-city"><svg width="9" height="10" viewBox="0 0 9 10"><path d="M4.5 0a3.3 3.3 0 0 1 3.3 3.3C7.8 5.6 4.5 8.2 4.5 8.2S1.2 5.6 1.2 3.3A3.3 3.3 0 0 1 4.5 0Z" fill="var(--paper)"/><circle cx="4.5" cy="3.3" r="1.2" fill="var(--ink)"/><rect x="0" y="9" width="9" height="1" fill="var(--paper)"/></svg>Orange County</div>
    <div class="contact-phone"><svg width="10" height="10" viewBox="0 0 10 10"><circle cx="5" cy="5" r="4.3" fill="none" stroke="var(--paper)" stroke-width="1.2"/><path d="M3.4 2.8l1 1-.6.8c.4.8 1 1.4 1.7 1.8l.8-.6 1 1-.8.9C4.9 7.5 2.6 5.3 2.5 3.5Z" fill="var(--paper)"/></svg>(714) 555-0178</div>
  </div>
  <div class="trainer"><span class="trainer-name">Dana Whitfield</span><br>Professional Dog<br>Trainer</div>
  <p class="site">www.BrightMeadowDogTraining.com</p>
</section>

<section class="rack-card rack-card--special">
  <svg class="card-shape" width="349" height="848" viewBox="0 0 349 848" aria-hidden="true">
    <path d="M0 0H349V210C300 225 270 240 230 236C170 230 120 180 0 196Z" fill="var(--paper)"/>
    <path d="M0 186C110 168 170 218 230 226C270 231 305 218 349 200V210C305 232 270 242 230 238C170 232 120 186 0 204Z" fill="var(--ink)"/>
    <path d="M0 688C70 680 130 690 190 672C250 652 290 628 349 640V848H0Z" fill="var(--ink)"/>
  </svg>

  <div class="brand" style="left:19px;top:44px"><span class="brand-dot"></span>Bright<br>Meadow</div>
  <h1 class="headline" style="left:18px;top:107px">We specialize in<br><b>Blind/Deaf</b><br><b>Dog Training</b></h1>
  <div class="photo" role="img" aria-label="Beagle sitting" style="left:192px;top:25px;width:147px;height:176px;border-radius:45% 45% 20% 20%;background:radial-gradient(circle at 45% 40%,#c98a4a,#e8ddd0 60%,transparent 72%)"></div>

  <h2 class="section-title" style="left:20px;top:214px">Deaf Dog Training</h2>
  <ul class="bullets bullets--tight" style="left:19px;top:238px;width:185px">
    <li>Deaf dogs can easily be trained using hand signals.</li>
    <li>We owe it to our dogs to teach them how to behave, and that the world is a safe place.</li>
    <li>A dog with special needs is no exception.</li>
    <li>Training a dog that is deaf can come with it challenges.</li>
  </ul>
  <div class="photo photo--round" role="img" aria-label="Tricolor shepherd dog at the beach" style="left:211px;top:252px;width:104px;height:104px;background:linear-gradient(var(--photo-sky),#d8cdbf 55%,#6b4a35)"></div>

  <div class="photo photo--round" role="img" aria-label="Smiling golden retriever" style="left:24px;top:371px;width:103px;height:103px;background:radial-gradient(circle,#d19a55,#9c6330)"></div>
  <h2 class="section-title" style="left:137px;top:373px">Blind Dog Training</h2>
  <ul class="bullets bullets--tight" style="left:134px;top:393px;width:195px">
    <li>Deaf dogs can easily be trained using sound signals.</li>
    <li>A dog with special needs is no exception.</li>
    <li>Owners can wear a jingling bell, so your blind dog can find you. Blind Dogs have EXTREMELY heightened senses (especially smell and sound).</li>
  </ul>

  <h2 class="section-title" style="left:20px;top:513px">Deaf / Blind Dog Training</h2>
  <ul class="bullets bullets--tight" style="left:19px;top:534px;width:170px">
    <li>Deaf/Blind dogs can easily be trained using touch and tactile cues.</li>
    <li>A dog with special needs is no exception.</li>
    <li>Training a dog that is both blind and deaf can come with its own challenges, we have many years of experience to help.</li>
  </ul>
  <div class="photo photo--round" role="img" aria-label="White dog wearing a service vest near a tree" style="left:211px;top:522px;width:103px;height:103px;background:linear-gradient(120deg,var(--photo-green),#e6e3dc 55%,#6d5a47)"></div>

  <div class="photo" role="img" aria-label="Trainer kneeling with a shepherd dog" style="left:245px;top:667px;width:104px;height:181px;background:linear-gradient(160deg,#8c7a66,#4b5166 60%,#7a6045)"></div>

  <p class="cta">Schedule <b>Free 30 Minute</b><br>Phone Consultation With</p>
  <div class="contacts">
    <div class="contact-city"><svg width="9" height="10" viewBox="0 0 9 10"><path d="M4.5 0a3.3 3.3 0 0 1 3.3 3.3C7.8 5.6 4.5 8.2 4.5 8.2S1.2 5.6 1.2 3.3A3.3 3.3 0 0 1 4.5 0Z" fill="var(--paper)"/><circle cx="4.5" cy="3.3" r="1.2" fill="var(--ink)"/><rect x="0" y="9" width="9" height="1" fill="var(--paper)"/></svg>Los Angeles</div>
    <div class="contact-phone"><svg width="10" height="10" viewBox="0 0 10 10"><circle cx="5" cy="5" r="4.3" fill="none" stroke="var(--paper)" stroke-width="1.2"/><path d="M3.4 2.8l1 1-.6.8c.4.8 1 1.4 1.7 1.8l.8-.6 1 1-.8.9C4.9 7.5 2.6 5.3 2.5 3.5Z" fill="var(--paper)"/></svg>(310) 555-0142</div>
    <div class="contact-city"><svg width="9" height="10" viewBox="0 0 9 10"><path d="M4.5 0a3.3 3.3 0 0 1 3.3 3.3C7.8 5.6 4.5 8.2 4.5 8.2S1.2 5.6 1.2 3.3A3.3 3.3 0 0 1 4.5 0Z" fill="var(--paper)"/><circle cx="4.5" cy="3.3" r="1.2" fill="var(--ink)"/><rect x="0" y="9" width="9" height="1" fill="var(--paper)"/></svg>Orange County</div>
    <div class="contact-phone"><svg width="10" height="10" viewBox="0 0 10 10"><circle cx="5" cy="5" r="4.3" fill="none" stroke="var(--paper)" stroke-width="1.2"/><path d="M3.4 2.8l1 1-.6.8c.4.8 1 1.4 1.7 1.8l.8-.6 1 1-.8.9C4.9 7.5 2.6 5.3 2.5 3.5Z" fill="var(--paper)"/></svg>(714) 555-0178</div>
  </div>
  <div class="trainer"><span class="trainer-name">Dana Whitfield</span><br>Professional Dog<br>Trainer</div>
  <p class="site">www.QuietPawsDogTraining.com</p>
</section>

</body>
</html>
```